New Business Card Design for Manufacturing

We are an engineering/manufacturing company that offers Advanced machining/assembly/engineering services, as well as innovative products for the heavy duty engine cooling markets.

We are looking to get a new business card designed that is clean and modern looking, but still fits the wide range of technical/skilled work we do.

- We hope to use this design as the base for other design work in new Presentations, web, and print work.

Industry/Entity Type

Engineering

Contact Information for Business Card

Our preferred color of blue is (RGB) 22/71/159 but can vary slightly from that color. Our content will be our Logo and full company name (Vantrell Forge Works, Inc.), company address, name, job title, phone number with extension, cell number, fax number, website, and email address on the cards.
We'd like the full company name next to the logo, but we are open to other interpretations of that layout.
Preferably, we would like the back side to be clean with just our logo, and the front to contain all of the contact information.

Colors
2f74b4
0355a3
85abd2

Requirements
Must have
• - Logo, company name, needed content - We are open to interpretation beyond that.
• - Standard size business card.
• - Horizontal orientation.
• - Enough space for lengthy names / job titles (for example, a job title could read "Directory of Human Resources" or "V.P. of Governmental Affairs"). We need this to look clean, whether the title be short (CEO) or long (as described above).

```html
<!DOCTYPE html>
<html lang="en">
<head>
<meta charset="utf-8">
<title>Vantrell Forge Works – Business Card</title>
<link rel="stylesheet" href="https://fonts.googleapis.com/css2?family=Montserrat:wght@800&family=Open+Sans:wght@400;600&display=swap">
<style>
  :root {
    --backdrop: #3b3b3d;
    --card: #1e1e20;
    --brand-blue: #1a5fb4;
    --band-blue: #0f6fcf;
    --band-blue-dark: #0355a3;
    --steel: #9aa4ae;
    --gloss: #4a4a4e;
    --gloss-light: #6e6e74;
    --text-light: #f2f2f2;
  }
  * { box-sizing: border-box; margin: 0; padding: 0; }
  html, body { width: 799px; height: 1200px; overflow: hidden; }
  body {
    background: var(--backdrop);
    display: flex;
    flex-direction: column;
    align-items: center;
    justify-content: space-around;
    padding: 90px 0;
    font-family: "Open Sans", sans-serif;
  }
  .card {
    position: relative;
    width: 620px;
    height: 354px;
    background: var(--card);
    border-radius: 4px;
    overflow: hidden;
    box-shadow: 0 14px 30px rgba(0,0,0,.45);
  }

  /* Back side */
  .card-back {
    display: flex;
    flex-direction: column;
    align-items: center;
    justify-content: center;
    gap: 14px;
  }
  .back-name {
    font-family: "Montserrat", sans-serif;
    font-weight: 800;
    font-size: 40px;
    letter-spacing: 1px;
    text-transform: uppercase;
    color: var(--gloss);
  }
  .back-tagline {
    font-family: "Montserrat", sans-serif;
    font-weight: 800;
    font-size: 20px;
    letter-spacing: 2px;
    text-transform: uppercase;
    color: var(--gloss-light);
  }

  /* Front side */
  .company {
    position: absolute;
    left: 30px;
    top: 58px;
    width: 270px;
  }
  .company-name {
    font-family: "Montserrat", sans-serif;
    font-weight: 800;
    font-size: 30px;
    line-height: 1.08;
    text-transform: uppercase;
    color: var(--brand-blue);
  }
  .company-rule {
    margin-top: 14px;
    height: 2px;
    width: 250px;
    background: var(--steel);
  }
  .contact {
    position: absolute;
    left: 340px;
    top: 56px;
    color: var(--text-light);
  }
  .contact-name {
    font-size: 22px;
    font-weight: 600;
    color: var(--brand-blue);
    line-height: 1.1;
  }
  .contact-title {
    font-size: 12.5px;
    margin-bottom: 12px;
  }
  .contact-list { list-style: none; font-size: 13.5px; line-height: 21px; }
  .contact-list li { display: flex; align-items: center; gap: 8px; }
  .contact-list svg { width: 12px; height: 12px; fill: var(--brand-blue); flex: none; }
  .contact-address { margin-top: 4px; font-size: 13.5px; line-height: 19px; }

  .steel-stripe {
    position: absolute;
    left: 0;
    right: 0;
    top: 290px;
    height: 9px;
    background: var(--steel);
  }
  .tagline-band {
    position: absolute;
    left: 250px;
    right: 0;
    bottom: 0;
    height: 72px;
    border-top-left-radius: 26px;
    background: linear-gradient(90deg, var(--band-blue), var(--band-blue-dark));
    display: flex;
    align-items: center;
    padding-left: 30px;
  }
  .tagline {
    font-family: "Montserrat", sans-serif;
    font-weight: 800;
    font-size: 19px;
    letter-spacing: 1px;
    text-transform: uppercase;
    color: var(--text-light);
  }
</style>
</head>
<body>

  <section class="card card-back" aria-label="Card back">
    <div class="back-name">Vantrell Forge Works</div>
    <div class="back-tagline">Precision in Motion</div>
  </section>

  <section class="card card-front" aria-label="Card front">
    <div class="company">
      <div class="company-name">Vantrell Forge Works, Inc.</div>
      <div class="company-rule"></div>
    </div>

    <div class="contact">
      <div class="contact-name">John Doe Smith</div>
      <div class="contact-title">Managing Director</div>
      <ul class="contact-list">
        <li>
          <svg viewBox="0 0 12 12" aria-hidden="true"><path d="M2 1h2.5l1 3-1.5 1a6 6 0 0 0 3 3l1-1.5 3 1V10a1 1 0 0 1-1 1A9 9 0 0 1 1 2a1 1 0 0 1 1-1z"/></svg>
          111-2222-2222 (EXT)
        </li>
        <li>
          <svg viewBox="0 0 12 12" aria-hidden="true"><path d="M3 0h6a1 1 0 0 1 1 1v10a1 1 0 0 1-1 1H3a1 1 0 0 1-1-1V1a1 1 0 0 1 1-1zm0 1.5v7.5h6V1.5z"/></svg>
          333-3333-3333
        </li>
        <li>
          <svg viewBox="0 0 12 12" aria-hidden="true"><path d="M3 0h6v3H3zM1 4h10a1 1 0 0 1 1 1v4H10v3H2V9H0V5a1 1 0 0 1 1-1zm2 5v2h6V9z"/></svg>
          444-4444-4444
        </li>
        <li>
          <svg viewBox="0 0 12 12" aria-hidden="true"><path d="M6 0a6 6 0 1 0 0 12A6 6 0 0 0 6 0zm0 1.3a4.7 4.7 0 1 1 0 9.4 4.7 4.7 0 0 1 0-9.4zM1.5 5.4h9v1.2h-9zM5.4 1.5h1.2v9H5.4z"/></svg>
          www.yourwebsite.com
        </li>
        <li>
          <svg viewBox="0 0 12 12" aria-hidden="true"><path d="M0 2h12v8H0zm1.2 1.2V4L6 7l4.8-3v-.8L6 6.2z"/></svg>
          johndoe@yourwebsite.com
        </li>
      </ul>
      <div class="contact-address">234 Anywhere St., Any City,<br>Any Town, US 123456</div>
    </div>

    <div class="steel-stripe"></div>
    <div class="tagline-band">
      <span class="tagline">Precision in Motion</span>
    </div>
  </section>

</body>
</html>
```